Roofing company in Toronto, Canada needs a logo design and business card design

We need a business card and logo created for our company. Our company is "KLV Roofing" which provides roofing services for commercial and residential customers. We serve customers in the Greater Toronto Area (in Canada) thus the name KLV.

We want the logo and business card to be a modern design displaying professionalism and quality in the work. We would prefer rounded corners for the business cards but are open to other ideas. The cards should be pleasant and appealing to customers.

Target Market(s)

Commercial and Residential customers

Industry/Entity Type

Roofing

Contact Information for Business Card

Logo Text

KLV Roofing

Requirements
Nice to have
• Colours that are pleasing to the eye but at the same time should stand out from other business cards. If the design can incorporate the name of KLV Roofing and the actual concept of roofing that would be nice.
Should not have
• Do not want the business cards or logo to be childish looking. Need to look professionally designed.

```html
<!DOCTYPE html>
<html lang="en">
<head>
<meta charset="utf-8">
<title>KLV Roofing – Business Cards</title>
<link rel="stylesheet" href="https://fonts.googleapis.com/css2?family=Lato:wght@400;700;900&display=swap">
<style>
  :root {
    --backdrop: #6a6a6a;
    --card-dark: #1f1f1f;
    --brand-yellow: #fbb900;
    --band-yellow: #e7a70c;
    --ink-dark: #2a2a2a;
    --text-light: #e6e6e6;
  }
  * { box-sizing: border-box; margin: 0; padding: 0; }
  html, body {
    width: 1200px;
    height: 900px;
    overflow: hidden;
    background: var(--backdrop);
    font-family: "Lato", sans-serif;
  }
  .card {
    position: absolute;
    width: 500px;
    height: 286px;
    border-radius: 24px;
    overflow: hidden;
  }
  .card--front {
    left: 600px;
    top: 170px;
    background: var(--brand-yellow);
    display: flex;
    align-items: center;
    justify-content: center;
  }
  .card--back {
    left: 110px;
    top: 440px;
    background: var(--card-dark);
  }
  .wordmark {
    font-family: "Lato", sans-serif;
    font-weight: 900;
    text-transform: uppercase;
    line-height: 0.95;
    text-align: center;
  }
  .wordmark__main { display: block; font-size: 78px; letter-spacing: 2px; }
  .wordmark__sub { display: block; font-size: 38px; letter-spacing: 4px; }
  .card--front .wordmark { color: var(--ink-dark); }
  .card--back .wordmark {
    position: absolute;
    right: 44px;
    top: 78px;
    color: var(--brand-yellow);
  }
  .card--back .wordmark__main { font-size: 64px; }
  .card--back .wordmark__sub { font-size: 31px; }
  .holder {
    position: absolute;
    left: 30px;
    top: 30px;
  }
  .holder__name {
    color: var(--brand-yellow);
    font-weight: 900;
    font-size: 13px;
    letter-spacing: 0.5px;
    text-transform: uppercase;
  }
  .holder__role {
    color: var(--text-light);
    font-size: 11px;
    margin-top: 2px;
  }
  .contact-list {
    position: absolute;
    left: 30px;
    top: 112px;
    list-style: none;
  }
  .contact-list li {
    display: flex;
    align-items: center;
    gap: 8px;
    color: var(--text-light);
    font-size: 12.5px;
    line-height: 19px;
  }
  .contact-list svg { width: 10px; height: 10px; fill: var(--brand-yellow); flex: none; }
  .address-band {
    position: absolute;
    left: 0; right: 0; bottom: 0;
    height: 58px;
    background: var(--band-yellow);
    display: flex;
    align-items: center;
    justify-content: center;
    color: var(--ink-dark);
    font-size: 13px;
    letter-spacing: 0.3px;
  }
</style>
</head>
<body>
  <section class="card card--front" aria-label="Business card front">
    <div class="wordmark">
      <span class="wordmark__main">KLV</span>
      <span class="wordmark__sub">Roofing</span>
    </div>
  </section>

  <section class="card card--back" aria-label="Business card back">
    <div class="holder">
      <p class="holder__name">Marcus Delaney</p>
      <p class="holder__role">Managing Director</p>
    </div>

    <ul class="contact-list">
      <li>
        <svg viewBox="0 0 10 10" aria-hidden="true"><path d="M2 0.5 L3.6 2.6 L2.8 3.6 Q4 6 6.4 7.2 L7.4 6.4 L9.5 8 L8.3 9.5 Q3 9 0.5 1.7 Z"/></svg>
        416-555-0142
      </li>
      <li>
        <svg viewBox="0 0 10 10" aria-hidden="true"><path d="M2.5 0 H7.5 A1 1 0 0 1 8.5 1 V9 A1 1 0 0 1 7.5 10 H2.5 A1 1 0 0 1 1.5 9 V1 A1 1 0 0 1 2.5 0 Z M2.6 1.4 V7.8 H7.4 V1.4 Z"/></svg>
        416-555-0143
      </li>
      <li>
        <svg viewBox="0 0 10 10" aria-hidden="true"><path d="M0 1.5 H10 V8.5 H0 Z M0.8 2.2 L5 5.4 L9.2 2.2 Z" fill-rule="evenodd"/></svg>
        info@klvroofing.ca
      </li>
      <li>
        <svg viewBox="0 0 10 10" aria-hidden="true"><circle cx="5" cy="5" r="4.6"/><path d="M0.6 5 H9.4 M5 0.4 Q2.4 5 5 9.6 M5 0.4 Q7.6 5 5 9.6" stroke="#1f1f1f" stroke-width="0.8" fill="none"/></svg>
        www.klvroofing.ca
      </li>
    </ul>

    <div class="wordmark">
      <span class="wordmark__main">KLV</span>
      <span class="wordmark__sub">Roofing</span>
    </div>

    <div class="address-band">48 Lakeshore Road, Toronto ON M5V 2T6</div>
  </section>
</body>
</html>
```